Business cards - BRENT Roofing & Siding

We need simple business cards made up for our Roofing & Siding business based in Calgary Alberta.
The logo on one side of the card and potentially our slogan "Built with trust, verified by time".
The other side could have:
-A small logo
-Rep name:
-Rep cell phone:
-Rep email:
-Office phone: 403-684-2093
-Website: PrairieShingleWorks.com

We would like to incorporate the colours from our logo, especially the lite blue on the jpeg file. I have attached the ai file and jpeg file. We like the colours better on the jpeg file.

I do not require a money back guarantee

```html
<!DOCTYPE html>
<html lang="en">
<head>
<meta charset="utf-8">
<title>BRENT Roofing &amp; Siding – Business Cards</title>
<link href="https://fonts.googleapis.com/css2?family=Montserrat:wght@400;700&display=swap" rel="stylesheet">
<style>
  :root {
    --brand-blue: #0467b9;
    --accent-blue: #1e88e5;
    --ink: #3a3a3a;
    --paper: #ffffff;
    --backdrop: #e9ebee;
  }
  * { box-sizing: border-box; margin: 0; padding: 0; }
  html, body { width: 1200px; height: 900px; overflow: hidden; }
  body {
    background: var(--backdrop);
    font-family: "Montserrat", Arial, sans-serif;
    position: relative;
  }
  .card {
    position: absolute;
    left: 250px;
    width: 700px;
    height: 400px;
    box-shadow: 0 6px 18px rgba(0,0,0,0.18);
  }
  .card-front {
    top: 35px;
    background: var(--brand-blue);
    display: flex;
    align-items: center;
    justify-content: center;
  }
  .card-back {
    top: 465px;
    background: var(--paper);
    display: flex;
    align-items: center;
  }
  .wordmark {
    display: flex;
    align-items: center;
    gap: 14px;
    font-weight: 700;
    letter-spacing: 2px;
    white-space: nowrap;
  }
  .wordmark-square { width: 18px; height: 18px; flex: none; }
  .card-front .wordmark { color: var(--paper); font-size: 34px; }
  .card-front .wordmark-square { background: var(--paper); }
  .card-back .wordmark { color: var(--brand-blue); font-size: 22px; letter-spacing: 1.5px; }
  .card-back .wordmark-square { background: var(--brand-blue); width: 14px; height: 14px; }
  .back-logo {
    width: 380px;
    display: flex;
    justify-content: center;
    padding-left: 30px;
  }
  .divider {
    width: 1.5px;
    height: 170px;
    background: var(--accent-blue);
  }
  .contact {
    padding-left: 36px;
    color: var(--ink);
  }
  .rep-name {
    color: var(--accent-blue);
    font-weight: 700;
    font-size: 26px;
    letter-spacing: 0.5px;
    line-height: 1;
  }
  .rep-title {
    font-size: 15px;
    letter-spacing: 0.5px;
    margin: 6px 0 14px;
  }
  .contact-list { list-style: none; }
  .contact-list li {
    display: flex;
    align-items: center;
    gap: 10px;
    font-size: 15px;
    line-height: 26px;
  }
  .contact-icon { width: 13px; height: 13px; flex: none; color: var(--accent-blue); }
</style>
</head>
<body>
  <section class="card card-front" aria-label="Card front">
    <div class="wordmark"><span class="wordmark-square"></span>BRENT Roofing &amp; Siding</div>
  </section>

  <section class="card card-back" aria-label="Card back">
    <div class="back-logo">
      <div class="wordmark"><span class="wordmark-square"></span>BRENT Roofing &amp; Siding</div>
    </div>
    <div class="divider"></div>
    <div class="contact">
      <h1 class="rep-name">DANIEL KERR</h1>
      <p class="rep-title">DIRECTOR</p>
      <ul class="contact-list">
        <li>
          <svg class="contact-icon" viewBox="0 0 16 16" aria-hidden="true"><path fill="currentColor" d="M3.6 1.5l2.3 2.6-1.3 1.7c.9 2 2.6 3.7 4.6 4.6l1.7-1.3 2.6 2.3-1.4 2.3C6.8 13.4 2.6 9.2 1.3 3z"/></svg>
          403-684-2093
        </li>
        <li>
          <svg class="contact-icon" viewBox="0 0 16 16" aria-hidden="true"><rect x="4" y="1" width="8" height="14" rx="1.5" fill="none" stroke="currentColor" stroke-width="1.6"/><circle cx="8" cy="12.3" r="0.9" fill="currentColor"/></svg>
          905-431-7788
        </li>
        <li>
          <svg class="contact-icon" viewBox="0 0 16 16" aria-hidden="true"><rect x="1.5" y="3.5" width="13" height="9" fill="none" stroke="currentColor" stroke-width="1.5"/><path d="M1.5 3.5L8 9l6.5-5.5" fill="none" stroke="currentColor" stroke-width="1.5"/></svg>
          brentroof@prairiemail.net
        </li>
        <li>
          <svg class="contact-icon" viewBox="0 0 16 16" aria-hidden="true"><g fill="none" stroke="currentColor" stroke-width="1.3"><circle cx="8" cy="8" r="6.5"/><ellipse cx="8" cy="8" rx="2.8" ry="6.5"/><path d="M1.5 8h13M2.6 4.6h10.8M2.6 11.4h10.8"/></g></svg>
          prairieshingleworks.com
        </li>
      </ul>
    </div>
  </section>
</body>
</html>
```